NCCS Brochure Design

Northfield Council of Clinical Standards (NCCS) needs a whole new brochure. I've upload EPS logos and past brochures. Our tagline is to "modernize healthcare" and we think our brochure should reflect that, so that's the purpose of this project.

NCCS is a proven leader in healthcare education, training and
consulting services for health professionals. We’ve earned a reputation for excellence in healthcare quality improvement and management.

NCCS works to improve healthcare quality by educating healthcare professionals about healthcare best practices. We focus on instructing our clients on how to plan for, measure, and improve healthcare quality in all facilities and facets such as:

Patient Safety
Infection Control
Performance Improvement
Risk Management
Compliance and Accreditation
Health and Hospital Administration
Health Insurance
Healthcare Financial Management
Facility Management and Safety

DESIGN SUGGESTIONS:

Brochure Size: 8.5 X 11 full size brochure or 8.5 X 11 trifold brochure

Number of Pages: 2 to 3

Colors: Feel free to use a wide array of colors but try to stay away from colors that are too loud, ex: Pink, Purple, Neon Green.

Themes: Professional, Educational

Designs:

Pelvor by Tobin Haskell

Lumora Leaflet by Derek Molloy

Gears of assembly by Vostrelle

Figura de Mr KB by qzpt

http://www.plimvaro.com/post/28461937520/10-creative-brochure-designs

Don't limit yourself to these examples. However, these are examples we liked

Reason: We would like to see more designs

We want more full page designs than tri-fold 

We are considering both tri-fold and full-page but would like to see more full page designs 

Reason: Our lead designer making the decisions on this project has been fired. I apologize for the inconvenience. We want extend the project one last time

Target Market(s)

Students, Doctors, and Educational Professionals

Industry/Entity Type

Healthcare

Font styles to use
Serif
Sans Serif
Decorative
Script

Requirements
Should not have
• Pink, Purple, Neon Green colors

```html
<!DOCTYPE html>
<html lang="en">
<head>
<meta charset="utf-8">
<title>NCCS Brochure – Inside Spread</title>
<link rel="stylesheet" href="https://fonts.googleapis.com/css2?family=Michroma&family=Open+Sans:wght@400;600;700&display=swap">
<style>
:root{
  --canvas:#e4e4e4;
  --panel-grey:#a6a8a9;
  --panel-grey-light:#b9bbbc;
  --band-dark:#3b3c3d;
  --band-darker:#2a2b2c;
  --ink:#2f3030;
  --ink-soft:#4a4b4c;
  --paper-white:#f4f6f6;
  --teal-light:#d3dede;
  --teal-mid:#8ea2a5;
  --teal-deep:#4c5d60;
}
*{box-sizing:border-box;margin:0;padding:0}
html,body{width:1200px;height:1000px;overflow:hidden;background:var(--canvas);font-family:"Open Sans",Arial,sans-serif}
.brochure{position:absolute;left:60px;top:150px;width:1080px;height:700px;display:flex;box-shadow:0 18px 40px rgba(0,0,0,.22)}
.panel{position:relative;width:360px;height:700px;overflow:hidden}
.panel + .panel{border-left:1px solid rgba(0,0,0,.18)}
.heading-display{font-family:"Michroma",sans-serif;letter-spacing:2px;text-transform:uppercase}
.photo{position:absolute}

/* Left panel */
.panel-purpose .photo{inset:0;background:linear-gradient(172deg,var(--teal-light) 0%,#e6ecec 30%,#dfe6e6 62%,var(--teal-mid) 70%,#2d3436 82%,#3c4547 92%,var(--teal-mid) 100%)}
.intro-band{position:absolute;left:0;top:0;width:360px;height:120px;background:var(--band-dark);clip-path:polygon(0 0,100% 0,100% 100%,12% 100%,0 80%);padding:18px 22px 0 70px;color:var(--paper-white);font-size:10.5px;line-height:1.45;font-weight:600}
.intro-band .mark{position:absolute;right:22px;bottom:10px;width:20px;height:20px;border-radius:50%;background:var(--paper-white)}
.statement{position:absolute;left:24px;width:200px;color:var(--ink)}
.statement h2{font-size:20px;margin-bottom:6px}
.statement p{font-size:9.5px;line-height:1.45;font-weight:600}
.vision{top:170px}
.mission{top:330px}

/* Middle panel */
.panel-courses{background:var(--panel-grey)}
.section-band{position:absolute;left:0;top:24px;height:40px;background:var(--band-dark);color:var(--paper-white);display:flex;align-items:center;padding-left:22px;font-size:15px}
.panel-courses .section-band{width:340px;clip-path:polygon(0 0,92% 0,100% 50%,92% 100%,0 100%)}
.course-list{position:absolute;left:24px;top:78px;list-style:none;font-size:9.5px;line-height:1.55;color:var(--paper-white);font-weight:600}
.web-box{position:absolute;left:22px;top:232px;width:300px;height:62px;border:2px solid var(--ink-soft);border-radius:12px;padding:6px 14px;color:var(--ink)}
.web-box .note{font-size:9px;font-weight:700}
.web-box .url{font-size:24px;color:var(--ink-soft);letter-spacing:1px}
.web-box svg{position:absolute;right:-10px;bottom:-16px}
.team{position:absolute;left:24px;top:310px;width:150px;color:var(--ink)}
.block-title{font-size:17px;color:var(--ink-soft);margin-bottom:6px}
.team p{font-size:9px;line-height:1.45;font-weight:600;margin-bottom:8px}
.team ul{list-style:none;font-size:9px;line-height:1.5;font-weight:600}
.panel-courses .photo{left:182px;top:320px;width:160px;height:170px;background:linear-gradient(150deg,#f2f4f4,#b7c9cc 50%,#dde4e4);border:3px solid var(--paper-white)}
.about{position:absolute;left:0;top:500px;width:360px;height:200px;background:var(--panel-grey-light);clip-path:polygon(0 12%,12% 0,100% 0,100% 100%,0 100%);padding:26px 24px 0;color:var(--ink)}
.about p{font-size:9.5px;line-height:1.5;font-weight:600}

/* Right panel */
.panel-schedule .photo{inset:0;background:linear-gradient(170deg,#6c7c7f 0%,var(--teal-deep) 40%,var(--teal-mid) 65%,#5a6a6d 100%)}
.panel-schedule .section-band{width:360px;background:var(--band-darker);clip-path:polygon(6% 0,100% 0,100% 100%,6% 100%,0 50%);padding-left:40px}
.schedule{position:absolute;left:24px;top:86px;width:310px;list-style:none;color:var(--paper-white)}
.schedule li{margin-bottom:13px;font-size:9.5px;line-height:1.45}
.schedule strong{display:block;font-weight:600}
.brand-block{position:absolute;left:0;bottom:0;width:360px;height:150px;background:var(--panel-grey);display:flex;align-items:center;justify-content:center}
.brand-block .name{font-weight:700;font-size:40px;color:var(--band-dark);letter-spacing:1px}
</style>
</head>
<body>
<main class="brochure">

  <section class="panel panel-purpose">
    <div class="photo" role="img" aria-label="Blurred photo of a medical professional walking through a hospital corridor"></div>
    <div class="intro-band">
      NCCS is a proven leader in healthcare education, training and consulting services for health professionals. We’ve earned a reputation for excellence in healthcare quality improvement and management.
      <span class="mark"></span>
    </div>
    <div class="statement vision">
      <h2 class="heading-display">Vision</h2>
      <p>Here at the Northfield Council of Clinical Standards, we believe every patient deserves care of the highest quality. We strive to be the trusted partner that helps professionals turn best practice into daily habit, raising standards in every facility we serve.</p>
    </div>
    <div class="statement mission">
      <h2 class="heading-display">Mission</h2>
      <p>Our mission is to modernize healthcare by educating the professionals who deliver it. We aim to give you the tools, knowledge and confidence to plan, measure and improve quality and to be true advocates for patient safety.</p>
    </div>
  </section>

  <section class="panel panel-courses">
    <h2 class="section-band heading-display">Course Offerings</h2>
    <ul class="course-list">
      <li>Healthcare Quality Foundations</li>
      <li>Infection Control in Practice</li>
      <li>Patient Safety Workshop</li>
      <li>Clinical Risk Workshop</li>
      <li>Health Services Leadership</li>
      <li>Hospital Administration Basics</li>
      <li>Budgeting for Care Teams</li>
      <li>Facility Safety and Compliance</li>
    </ul>
    <div class="web-box">
      <p class="note">For detailed Courses program Please visit our website</p>
      <p class="url">www.nccsquality.org</p>
      <svg width="30" height="34" viewBox="0 0 30 34" aria-hidden="true"><path d="M8 4v16l-3-3-3 3 7 10h14l3-12-9-3V4c0-3-6-3-6 0z" fill="#fff" stroke="#333" stroke-width="1.5"/></svg>
    </div>
    <div class="team">
      <h3 class="block-title heading-display">Our Team</h3>
      <p>Our outstanding advisory board brings decades of experience in hospital quality, safety and education.</p>
      <ul>
        <li>Dr. Helen Marsh</li>
        <li>Professor Owen Tally, PhD</li>
        <li>Professor Rita Vance, PhD</li>
        <li>Professor Sam Corrie, PhD</li>
      </ul>
    </div>
    <div class="photo" role="img" aria-label="Photo of a cheering team of doctors and nurses"></div>
    <div class="about">
      <h3 class="block-title heading-display">About Us</h3>
      <p>Here at the Northfield Council of Clinical Standards, we help health professionals plan for, measure and improve quality in all facilities. Our courses cover patient safety, infection control, risk management, compliance and accreditation, and hospital administration, giving learners practical skills they can use right away.</p>
    </div>
  </section>

  <section class="panel panel-schedule">
    <div class="photo" role="img" aria-label="Motion-blurred photo of a hospital hallway"></div>
    <h2 class="section-band heading-display">Course Schedule</h2>
    <ul class="schedule">
      <li><strong>Infection Control in Practice</strong>June 11–12, 2014 &nbsp;|&nbsp; 9:00 AM – 4:00 PM</li>
      <li><strong>Patient Safety Workshop</strong>June 18–19, 2014 &nbsp;|&nbsp; 9:00 AM – 4:00 PM</li>
      <li><strong>Healthcare Quality Foundations</strong>July 9–10, 2014 &nbsp;|&nbsp; 9:00 AM – 4:00 PM</li>
      <li><strong>Health Services Leadership</strong>July 23–24, 2014 &nbsp;|&nbsp; 9:00 AM – 4:00 PM</li>
      <li><strong>Clinical Risk Workshop</strong>August 6–7, 2014 &nbsp;|&nbsp; 9:00 AM – 4:00 PM</li>
      <li><strong>Budgeting for Care Teams</strong>August 20–21, 2014 &nbsp;|&nbsp; 9:00 AM – 4:00 PM</li>
    </ul>
    <div class="brand-block">
      <span class="name">NCCS</span>
    </div>
  </section>

</main>
</body>
</html>
```